Corporate Design für Abwicklung von Lohn- und Gehaltsabrechnungen
Super flexible Zusammenarbeit, alle Änderungen wurden zeitnah zur Ansicht geliefert. Sehr kreatives und einheitliches Ergebnis für das neue CI. Immer wieder gerne!!!
Zielgruppe
Wir wickeln die Lohn- und Gehaltsabrechnung für kleine bis mittlere Unternehmen ab.
Aufgabenstellung
Das bereits bestehende Logo kann gerne noch einmal, aber ähnlich von den Abmessungen und Farben her, geändert werden.
Insgesamt modernes und junges Auftreten.
Wichtig ist das Grün #3dae62
RGB 61 174 98
Wir wünschen uns ein einheitliches Corporate Design bestehend aus Briefpapier, Visitenkarten, Briefumschlägen und Schreibblöcken, angelehnt an das bereits vorhandene Logo.
Briefpapier, gerne 2-seitig mit grüner Rückseite
Endformat 210x297mm hoch
Visitenkarten 2-seitig, 85x55mm quer oder hoch (lassen uns gerne überraschen)
Die beigefügte Visitenkarte ist leider mit alten Daten, hat uns vom Prinzip her aber gut gefallen. Die neue sollte sich aber im Corporate Design Wiederspiegeln mit folgenden Daten:
Briefumschläge C4 (229 x 324mm Endformat) Hoch
Schreibblöcke A5 148x210 Endformat hoch
Schriftart Poppins

```html
<!DOCTYPE html>
<html lang="de">
<head>
<meta charset="utf-8">
<title>Schreibblock A5 – Veltmar</title>
<link href="https://fonts.googleapis.com/css2?family=Poppins:wght@400;500;600&display=swap" rel="stylesheet">
<style>
  :root {
    --brand-green: #3dae62;
    --brand-dark: #3a3a3a;
    --paper: #ffffff;
    --backdrop: #eef0f3;
    --grid-line: #a9adb2;
    --text-dark: #333333;
  }
  html, body {
    margin: 0;
    padding: 0;
    width: 1200px;
    height: 1200px;
    overflow: hidden;
    background: var(--backdrop);
    font-family: "Poppins", sans-serif;
  }
  .notepad {
    position: absolute;
    left: 212px;
    top: 50px;
    width: 775px;
    height: 1100px;
    background: var(--paper);
    box-shadow: 0 4px 18px rgba(0,0,0,0.08);
  }
  .brand-name {
    position: absolute;
    left: 62px;
    top: 48px;
    margin: 0;
    font-size: 50px;
    font-weight: 500;
    letter-spacing: -0.5px;
    color: var(--text-dark);
    line-height: 1;
  }
  .grid-area {
    position: absolute;
    left: 72px;
    top: 150px;
    width: 638px;
    height: 792px;
  }
  .website {
    position: absolute;
    left: 0;
    right: 70px;
    top: 958px;
    text-align: right;
    font-size: 22px;
    font-weight: 500;
    letter-spacing: 1px;
    line-height: 1.3;
    color: var(--text-dark);
    margin: 0;
  }
  .footer-bands {
    position: absolute;
    left: 0;
    top: 1000px;
    width: 775px;
    height: 50px;
  }
</style>
</head>
<body>
  <main class="notepad">
    <h1 class="brand-name">Veltmar</h1>

    <svg class="grid-area" viewBox="0 0 638 792" aria-hidden="true">
      <defs>
        <pattern id="grid-square" width="22" height="22" patternUnits="userSpaceOnUse">
          <path d="M22 0 L0 0 0 22" fill="none" stroke="var(--grid-line)" stroke-width="0.8"/>
        </pattern>
      </defs>
      <rect x="0" y="0" width="638" height="792" fill="url(#grid-square)"/>
      <rect x="0.4" y="0.4" width="637.2" height="791.2" fill="none" stroke="var(--grid-line)" stroke-width="0.8"/>
    </svg>

    <p class="website">www.veltmar.example</p>

    <svg class="footer-bands" viewBox="0 0 775 50" aria-hidden="true">
      <path class="band-green" d="M0 6 H540 Q562 6 562 28 V50 H0 Z" fill="var(--brand-green)"/>
      <rect class="band-dark" x="572" y="6" width="203" height="24" fill="var(--brand-dark)"/>
    </svg>
  </main>
</body>
</html>
```